Boutique custom software development company needs new business card

Our nearly 20 year old custom software development company would like to better include the fact that we are now providing Bitcoin services. These new services are B2B include education (how to acquire and securely hold Bitcoin) and integrating Bitcoin payments into existing ecommerce sites or other existing systems. Please keep the card clean and simple. Attached is our current design and some other files. vextorial.com

Target Market(s)

businesses owners interested in long term relationship

Industry/Entity Type

Custom software development and Bitcoin

Contact Information for Business Card

Dale Parker, dale@vextorial.com, vextorial.com, (888) 555-VXTRL

Font styles to use
Other font styles liked:
• monospace

Requirements
Must have
• double-sided
Nice to have
• clean and simple
Should not have
• physical address

```html
<!DOCTYPE html>
<html lang="en">
<head>
<meta charset="utf-8">
<title>Vextorial Business Card</title>
<link rel="stylesheet" href="https://fonts.googleapis.com/css2?family=Montserrat:wght@400;500;700;800&display=swap">
<style>
  :root {
    --backdrop: #3b3b3b;
    --card: #141414;
    --card-deep: #0a0a0a;
    --pattern-light: #2a2a2a;
    --blue: #3f78d1;
    --orange: #f47a20;
    --ink: #e9e9e9;
  }
  * { box-sizing: border-box; margin: 0; padding: 0; }
  html, body {
    width: 1200px; height: 801px; overflow: hidden;
    background: var(--backdrop);
    font-family: "Montserrat", Arial, sans-serif;
  }
  .canvas {
    position: relative; width: 1200px; height: 801px;
    display: flex; align-items: center; justify-content: center; gap: 50px;
  }
  .card {
    position: relative; width: 520px; height: 297px;
    background: var(--card);
    border-bottom: 2px solid var(--blue);
    border-left: 1px solid var(--blue);
    box-shadow: 0 18px 40px rgba(0,0,0,.45);
    overflow: hidden;
  }
  .brand-name {
    display: flex; align-items: center; gap: 8px;
    font-weight: 800; font-size: 30px; letter-spacing: 0.5px;
    color: var(--blue); line-height: 1;
  }
  .brand-mark { width: 13px; height: 13px; background: var(--orange); flex: none; }
  .brand-tagline {
    margin-top: 7px; padding-left: 21px;
    font-size: 11.5px; font-weight: 500; color: var(--blue);
    white-space: nowrap;
  }
  .brand-tagline .accent { color: var(--orange); }

  /* front */
  .card-front .brand { position: absolute; left: 40px; top: 122px; }
  .divider {
    position: absolute; left: 292px; top: 92px;
    width: 1px; height: 112px; background: var(--blue);
  }
  .contact { position: absolute; left: 312px; top: 98px; }
  .contact-name {
    font-weight: 700; font-size: 18px; color: var(--blue);
    text-transform: uppercase; margin-bottom: 12px; white-space: nowrap;
  }
  .contact-list { list-style: none; }
  .contact-item {
    display: flex; align-items: center; gap: 8px;
    font-size: 13px; color: var(--ink); margin-bottom: 7px; white-space: nowrap;
  }
  .contact-icon { width: 12px; height: 12px; flex: none; }

  /* back */
  .pattern-field {
    position: absolute; inset: 0;
    background: linear-gradient(135deg, var(--card-deep) 0%, var(--pattern-light) 55%, var(--card-deep) 100%);
  }
  .card-back .brand { position: absolute; right: 36px; top: 150px; }
</style>
</head>
<body>
<main class="canvas">
  <section class="card card-front" aria-label="Card front">
    <div class="brand">
      <div class="brand-name"><span class="brand-mark"></span>VEXTORIAL</div>
      <div class="brand-tagline">custom software &amp; <span class="accent">bitcoin services</span></div>
    </div>
    <div class="divider"></div>
    <div class="contact">
      <div class="contact-name">Dale Parker</div>
      <ul class="contact-list">
        <li class="contact-item">
          <svg class="contact-icon" viewBox="0 0 12 12"><path fill="var(--orange)" d="M3 1l2 2.4-1.2 1.2a7 7 0 0 0 3.6 3.6L8.6 7 11 9l-1.4 2C5 10.6 1.4 7 1 2.4z"/></svg>
          (888) 555-VXTRL
        </li>
        <li class="contact-item">
          <svg class="contact-icon" viewBox="0 0 12 12"><rect x="1" y="2.5" width="10" height="7" fill="var(--orange)"/><path d="M1 2.5l5 4 5-4" stroke="var(--card)" stroke-width="1" fill="none"/></svg>
          dale@vextorial.com
        </li>
        <li class="contact-item">
          <svg class="contact-icon" viewBox="0 0 12 12"><circle cx="6" cy="6" r="5" fill="var(--orange)"/><path d="M1 6h10M6 1c-2.5 3-2.5 7 0 10M6 1c2.5 3 2.5 7 0 10" stroke="var(--card)" stroke-width=".8" fill="none"/></svg>
          www.vextorial.com
        </li>
      </ul>
    </div>
  </section>

  <section class="card card-back" aria-label="Card back">
    <div class="pattern-field" role="img" aria-label="Repeating embossed gloss pattern of the brand symbol in black"></div>
    <div class="brand">
      <div class="brand-name"><span class="brand-mark"></span>VEXTORIAL</div>
      <div class="brand-tagline">custom software &amp; <span class="accent">bitcoin services</span></div>
    </div>
  </section>
</main>
</body>
</html>
```